Dental Patient Education Single page-Multiple pages needed.

I am creating a unique dental patient education materials for resale. I work in the dental industry, training dentists and thier teams how to improve patient acceptance rates for treatment. I see a need that all patient education material is designed incorrectly. I want to fix this by creating patient education material that educated patients based on all of the treatment options for a diagnosed condition. Tradidional patient education material reads like a catalog of procedures. This format is not effective for helping the patient quickly understand the consequences of non treatment and the benefits and disadvantages of their treatment options. Specifics of the Job:The design images must be royalty free.I will provide the text.Initially there are for major diagnosed conditions: Infected Tooth Treatment Options, Single to Multiple Missing tooth Treatment Options, Full Arch of Missing Teeth Treatment Options, and Full Arch Fixed Dental Implant Treatment OptionsThe layout should mirror the attached sample of Single Missing Tooth Treatment Options.This is a project that will require edits and redesigned based on testing.I also need this in Adobe, so it can be customized/branded for a dental office.

Target Market(s)

Dental office professionals to educate patients.

Font styles to use
Sans Serif

Colors
3277b5

Requirements
Must have
• Professional look and feel
• Royalty free images
• Easy to read

```html
<!DOCTYPE html>
<html lang="en">
<head>
<meta charset="utf-8">
<title>Single Missing Tooth – Treatment Options</title>
<link rel="stylesheet" href="https://fonts.googleapis.com/css2?family=Montserrat:wght@400;500;600;800&display=swap">
<style>
  :root {
    --brand-blue: #3277b5;
    --deep-blue: #1f63a6;
    --soft-grey: #b8bec6;
    --pale-grey: #e6e9ee;
    --ink: #333a42;
    --paper: #ffffff;
    --backdrop: #3a3b3e;
    --gum: #e6a1a6;
    --skin: #e9c4b0;
  }
  * { box-sizing: border-box; margin: 0; padding: 0; }
  html, body { width: 1200px; height: 776px; overflow: hidden; }
  body {
    background: var(--backdrop);
    font-family: "Montserrat", Arial, sans-serif;
    color: var(--ink);
    position: relative;
  }
  .page {
    position: absolute;
    top: 38px;
    width: 520px;
    height: 700px;
    background: var(--paper);
    overflow: hidden;
  }
  .page--cover { left: 60px; }
  .page--options { left: 620px; }
  .page-bg { position: absolute; inset: 0; width: 100%; height: 100%; }

  .image-slot { position: absolute; }
  .cover-photo {
    left: 110px; top: -50px; width: 440px; height: 440px;
    border-radius: 50%;
    background: radial-gradient(circle at 55% 55%, #f3d8c8 0%, var(--skin) 55%, #d9a893 100%);
    border: 4px solid var(--deep-blue);
  }
  .cover-title {
    position: absolute; left: 90px; top: 380px;
    color: var(--brand-blue); font-weight: 800;
    font-size: 44px; line-height: 1; letter-spacing: 0.5px;
    text-transform: uppercase;
  }
  .cover-subtitle {
    position: absolute; left: 92px; top: 476px;
    color: var(--brand-blue); font-weight: 500; font-size: 12px;
  }
  .cover-intro {
    position: absolute; right: 40px; top: 540px; width: 270px;
    text-align: right; font-size: 11.5px; line-height: 1.35; font-weight: 500;
  }
  .cover-intro p + p { margin-top: 12px; }
  .jaw-illustration {
    left: 0; top: 530px; width: 240px; height: 170px;
    border-radius: 0 60px 0 0;
    background: linear-gradient(160deg, #f4f4f4 0%, var(--gum) 55%, #c9737c 100%);
  }

  .option { position: absolute; }
  .option h2 {
    color: var(--brand-blue); font-weight: 800; font-size: 13px;
    line-height: 1.15; text-transform: uppercase; margin-bottom: 7px;
  }
  .option p { font-size: 8px; line-height: 1.4; text-align: justify; }
  .option--nothing { left: 42px; top: 62px; width: 220px; }
  .option--implant { left: 286px; top: 118px; width: 212px; }
  .option--bridge { left: 42px; top: 326px; width: 236px; }
  .option--partial { left: 296px; top: 478px; width: 200px; }

  .xray { right: 60px; top: 34px; width: 130px; height: 72px;
    background: linear-gradient(135deg, #2f3b4a, #8c98a6 60%, #3d4856); }
  .implant-diagram { left: 40px; top: 176px; width: 230px; height: 118px;
    background: linear-gradient(180deg, var(--gum) 0%, #f4eeee 60%, #ffffff 100%); border-radius: 6px; }
  .bridge-illustration { left: 300px; top: 328px; width: 196px; height: 118px;
    background: linear-gradient(180deg, var(--gum) 0%, #f7f3f3 60%, #ffffff 100%); border-radius: 6px; }
  .partial-illustration { left: 40px; top: 490px; width: 236px; height: 156px;
    background: linear-gradient(180deg, var(--gum) 0%, #f7f1f1 50%, #e59aa3 100%); border-radius: 6px; }
</style>
</head>
<body>

<section class="page page--cover">
  <svg class="page-bg" viewBox="0 0 520 700" aria-hidden="true">
    <path d="M0 40 H150 C40 180 10 420 120 700 H0 Z" fill="var(--soft-grey)"/>
    <path d="M0 80 C60 60 110 50 150 40 C60 180 40 420 150 700 H0 Z" fill="var(--brand-blue)"/>
    <path d="M0 140 C50 110 90 90 130 70 C60 220 60 450 180 700 H60 C20 520 10 300 0 260 Z" fill="var(--deep-blue)" opacity="0.55"/>
    <path d="M300 700 C380 640 460 600 520 590 V700 Z" fill="var(--pale-grey)"/>
  </svg>
  <div class="image-slot cover-photo" role="img" aria-label="Photo of a smiling woman's lower face showing healthy white teeth"></div>
  <h1 class="cover-title">Single<br>Missing Tooth</h1>
  <p class="cover-subtitle">A missing tooth is a serious issue. It can cause long-term</p>
  <div class="image-slot jaw-illustration" role="img" aria-label="Illustration of a lower jaw with a dental implant replacing one tooth"></div>
  <div class="cover-intro">
    <p>A missing tooth is a serious issue. It can cause long-term damage to facial structure, bone density and your ability to feel confident in your smile.</p>
    <p>Brightwell Dental Studio has several options available to fix your missing tooth.</p>
  </div>
</section>

<section class="page page--options">
  <svg class="page-bg" viewBox="0 0 520 700" aria-hidden="true">
    <path d="M0 0 H520 V40 C360 10 200 10 0 60 Z" fill="var(--brand-blue)"/>
    <path d="M0 0 H120 C70 20 30 40 0 60 Z" fill="var(--soft-grey)"/>
    <path d="M0 60 C200 14 360 14 520 44 V52 C360 26 200 26 0 70 Z" fill="var(--deep-blue)" opacity="0.5"/>
    <path d="M320 700 C420 620 480 540 520 500 V700 Z" fill="var(--pale-grey)"/>
  </svg>

  <div class="option option--nothing">
    <h2>Option 1:<br>Do Nothing</h2>
    <p>If you choose to do nothing at this time, the cost down the road can be substantial. $10,000+ for orthodontics to straighten out the teeth, implant, abutment and crown, bone grafting and possible sinus lift to replace lost bone.</p>
  </div>
  <div class="image-slot xray" role="img" aria-label="Dental X-ray showing the gap of a missing tooth"></div>

  <div class="option option--implant">
    <h2>Option 2:<br>Dental Implant</h2>
    <p>The bad news is that a dental implant is the most expensive option BUT the good news is it is the most effective, functional and aesthetically pleasing. A dental implant will keep the bone in that area of the jaw from atrophy. It helps maintain face shape and prevents 'sunken face'. The implant will prevent surrounding teeth from shifting and chances of losing the tooth decline. It will keep the teeth from shifting, and will prevent any future need to cut down the adjacent teeth. A dental implant is the nearest thing to a natural tooth available today.</p>
  </div>
  <div class="image-slot implant-diagram" role="img" aria-label="Diagram of an implant, abutment and crown placed in the upper jaw"></div>

  <div class="option option--bridge">
    <h2>Option 3:<br>Dental Bridge</h2>
    <p>The good news here is that a bridge is less expensive than the implant option BUT you will continue to lose bone in that area over time. Food will get caught in the hard to reach areas and if not cleaned properly could mean you have to replace the bridge every 7 years. In addition, to secure the bridge, the adjacent teeth must be cut down in order to be used as anchors for the appliance. Why cut down two good teeth if we don't have to?</p>
  </div>
  <div class="image-slot bridge-illustration" role="img" aria-label="Illustration of a three-unit dental bridge fitting onto prepared teeth"></div>

  <div class="image-slot partial-illustration" role="img" aria-label="Illustration of a removable partial denture fitting into the upper arch"></div>
  <div class="option option--partial">
    <h2>Option 4:<br>The Removable Partial<br>Denture (RPD)</h2>
    <p>The good news here is that it's the least expensive option of the 3, but the BAD news is that your teeth have to come out every night. You won't be able to chew your food as well and your tongue will be uncomfortable with the big, bulky plastic sitting in your mouth all day.</p>
  </div>
</section>

</body>
</html>
```